business card - Helicopter Flight Services, Flight School, etc.

We need a business card design for a new helicopter service.

We offer Helicopter Flight Services, Aerial Filming & Photography, Flight School, and Helicopter Tours. In that order.

Summit BladeAir, Inc.
Dennis Tollerby
SummitBladeair@Kestmail.com
626-418-7352

Based at the Brenwick Airport in Van Nuys, CA. The final design should communicate integrity and safety. Pictures or logos at your discretion.

Card back side - surprise me.

```html
<!DOCTYPE html>
<html lang="en">
<head>
<meta charset="utf-8">
<title>Summit BladeAir, Inc. — Business Card</title>
<link rel="stylesheet" href="https://fonts.googleapis.com/css2?family=Playfair+Display:wght@400;700&family=Arimo:wght@400&display=swap">
<style>
  :root {
    --backdrop: #e9e6e1;
    --card-black: #0b0b0c;
    --card-black-soft: #1c1c1e;
    --navy: #0b1450;
    --navy-deep: #050a33;
    --navy-band: #2a2f86;
    --sky-top: #e4edf6;
    --sky-bottom: #aebccd;
    --ink: #111111;
    --paper: #ffffff;
    --serif: "Playfair Display", Georgia, serif;
    --sans: "Arimo", Arial, sans-serif;
  }
  * { box-sizing: border-box; margin: 0; padding: 0; }
  html, body { width: 1200px; height: 892px; overflow: hidden; }
  body {
    background: var(--backdrop);
    position: relative;
  }
  .card {
    position: absolute;
    left: 290px;
    width: 620px;
    height: 354px;
    overflow: hidden;
    box-shadow: 0 6px 18px rgba(0,0,0,.18);
  }
  .card--front { top: 48px; background: var(--card-black); }
  .card--back {
    top: 490px;
    background: linear-gradient(160deg, var(--navy) 0%, var(--navy-deep) 100%);
    color: var(--paper);
    display: flex;
    flex-direction: column;
    align-items: center;
    justify-content: center;
  }
  .front-art { position: absolute; inset: 0; }
  .company-name {
    position: absolute;
    top: 30px;
    right: 34px;
    font-family: var(--serif);
    font-weight: 700;
    font-size: 30px;
    letter-spacing: 1px;
    color: var(--ink);
    text-transform: uppercase;
  }
  .holder-name {
    position: absolute;
    left: 40px;
    top: 232px;
    font-family: var(--serif);
    font-size: 24px;
    color: var(--paper);
  }
  .divider {
    position: absolute;
    left: 282px;
    top: 206px;
    width: 1px;
    height: 118px;
    background: var(--paper);
  }
  .contact-list {
    position: absolute;
    left: 304px;
    top: 212px;
    list-style: none;
    font-family: var(--sans);
    font-size: 17px;
    line-height: 1.3;
    color: var(--paper);
  }
  .contact-list li { display: flex; align-items: flex-start; gap: 9px; margin-bottom: 2px; }
  .contact-icon {
    flex: none;
    width: 14px; height: 14px;
    margin-top: 3px;
    background: var(--paper);
    border-radius: 2px;
    display: flex; align-items: center; justify-content: center;
  }
  .back-name {
    font-family: var(--serif);
    font-size: 38px;
    letter-spacing: 2px;
    text-transform: uppercase;
  }
  .back-services {
    margin-top: 8px;
    font-family: var(--serif);
    font-size: 24px;
    letter-spacing: .5px;
  }
</style>
</head>
<body>
  <section class="card card--front" aria-label="Card front">
    <svg class="front-art" width="620" height="354" viewBox="0 0 620 354">
      <defs>
        <linearGradient id="sky" x1="0" y1="0" x2="0" y2="1">
          <stop offset="0" stop-color="var(--sky-top)"/>
          <stop offset="1" stop-color="var(--sky-bottom)"/>
        </linearGradient>
        <linearGradient id="gloss" x1="0" y1="0" x2="1" y2="1">
          <stop offset="0" stop-color="var(--card-black-soft)"/>
          <stop offset="1" stop-color="var(--card-black)"/>
        </linearGradient>
      </defs>
      <rect width="620" height="354" fill="url(#gloss)"/>
      <polygon points="0,0 620,0 620,190 96,190 0,60" fill="var(--paper)"/>
      <polygon points="0,0 620,0 620,184 98,184 0,52" fill="var(--navy-band)"/>
      <polygon points="0,0 620,0 620,176 102,176 0,40" fill="var(--paper)"/>
      <polygon class="photo-area" role="img" aria-label="Photo of a helicopter flying in a pale sky above treetops"
               points="0,0 620,0 620,168 106,168 0,30" fill="url(#sky)"/>
    </svg>
    <h1 class="company-name">Summit BladeAir, Inc.</h1>
    <p class="holder-name">Dennis Tollerby</p>
    <span class="divider"></span>
    <ul class="contact-list">
      <li>
        <span class="contact-icon">
          <svg width="10" height="10" viewBox="0 0 10 10"><path d="M2 1 L4 1 L4.6 3 L3.4 3.8 Q4.4 5.8 6.2 6.6 L7 5.4 L9 6 L9 8 Q5 9 2 5 Q1 3 2 1 Z" fill="var(--card-black)"/></svg>
        </span>626-418-7352
      </li>
      <li>
        <span class="contact-icon">
          <svg width="10" height="10" viewBox="0 0 10 10"><rect x="1" y="2.5" width="8" height="5.5" fill="none" stroke="var(--card-black)" stroke-width="1"/><path d="M1 2.5 L5 5.6 L9 2.5" fill="none" stroke="var(--card-black)" stroke-width="1"/></svg>
        </span>SummitBladeair@Kestmail.com
      </li>
      <li>
        <span class="contact-icon">
          <svg width="10" height="10" viewBox="0 0 10 10"><path d="M5 9.4 Q1.6 5.6 1.6 3.8 A3.4 3.4 0 0 1 8.4 3.8 Q8.4 5.6 5 9.4 Z" fill="var(--card-black)"/><circle cx="5" cy="3.8" r="1.2" fill="var(--paper)"/></svg>
        </span>
        <span>2740 W. Larkfield Ave. Ste.A<br>Dorrance, CA 91588</span>
      </li>
    </ul>
  </section>

  <section class="card card--back" aria-label="Card back">
    <h2 class="back-name">Summit BladeAir, Inc.</h2>
    <p class="back-services">Airport · Tour guide · Helipad</p>
  </section>
</body>
</html>
```